Seeking a new website design for electrical contracting company

Brisket & Vane electrical contracting needs a new website for brisket-vane.example

We are looking for modern and something real cool with motion for a landing page. we have some cool images from our photo shoot. maybe even 3d motion our existing logo. we would like something we can edit with news and events and update a past project page. Also allow to take payment
stock images at
https://lorapellwinphotos.picvault-demo.example/Brisket-and-Vane

Target Market(s)

construction , home owners , business owners,

Industry/Entity Type

construction , electrical

Coding

Number of Pages Required

5+ page

Font styles to use
Serif
Sans Serif

Colors
0054AA
0677BA
7BADD7
CADEEF
E8F1F8
0094D4
00A9DD
6FCCEA
C7EBF8
E9F6FB
FFF300
FFF600
FEFA6F
FFFEC7
FFFEE8

Requirements
Must have
• excitement, motion, selling professionalism,

```html
<!DOCTYPE html>
<html lang="en">
<head>
<meta charset="utf-8">
<title>Brisket &amp; Vane — Electrical Contracting</title>
<link href="https://fonts.googleapis.com/css2?family=Montserrat:wght@400;500;600;700;800&display=swap" rel="stylesheet">
<style>
:root{
  --navy:#1e2460;
  --navy-deep:#171c4f;
  --orange:#f7941d;
  --ink:#1f2233;
  --body:#555a6b;
  --muted:#6b6f80;
  --mist:#e4e6f1;
  --tab:#dfe3f6;
  --white:#ffffff;
}
*{margin:0;padding:0;box-sizing:border-box}
html,body{width:1200px;height:5386px;overflow:hidden}
body{font-family:"Montserrat",Arial,sans-serif;color:var(--ink);background:var(--white);position:relative}
.abs{position:absolute}
.btn{position:absolute;display:flex;align-items:center;justify-content:center;gap:10px;background:var(--orange);color:var(--white);font-weight:700;font-size:12px;letter-spacing:.5px;text-transform:uppercase}

/* header + hero */
.hero{position:absolute;left:0;top:0;width:1200px;height:623px;background:linear-gradient(160deg,#5c6a86 0%,#3d4763 35%,#6d5c48 60%,#2c3150 100%)}
.hero::after{content:"";position:absolute;inset:0;background:linear-gradient(180deg,rgba(20,24,50,.55),rgba(20,24,50,.35) 50%,rgba(20,24,50,.6))}
.brand{position:absolute;left:100px;top:40px;display:flex;align-items:center;gap:12px;z-index:2;color:var(--white);font-weight:700;font-size:22px;letter-spacing:.3px}
.brand-mark{width:30px;height:30px;border:3px solid var(--white)}
.nav{position:absolute;left:483px;top:52px;display:flex;gap:28px;z-index:2}
.nav a{color:var(--white);text-decoration:none;font-size:12px;font-weight:600;letter-spacing:.3px}
.nav a.active{font-weight:700}
.quote{left:934px;top:40px;width:163px;height:42px;z-index:2;font-size:13px}
.hero-copy{position:absolute;left:0;width:1200px;top:180px;text-align:center;z-index:2;color:var(--white)}
.divider-mark{display:flex;align-items:center;justify-content:center;gap:14px}
.divider-mark span{display:block;width:52px;height:2px;background:var(--orange)}
.divider-mark i{display:block;width:34px;height:34px;border-radius:50%;border:4px solid currentColor}
.eyebrow{margin-top:22px;font-size:20px;font-weight:700;letter-spacing:.5px}
.hero h1{margin-top:14px;font-size:49px;line-height:55px;font-weight:800;letter-spacing:.5px}
.hero h1 .accent{color:var(--orange)}
.play{left:527px;top:478px;width:138px;height:40px;z-index:2}
.scroll-bowl{position:absolute;left:500px;top:523px;width:200px;height:200px;border-radius:50%;background:var(--mist)}
.scroll-btn{position:absolute;left:575px;top:592px;width:50px;height:50px;border-radius:50%;background:#3a4060;border:2px solid rgba(255,255,255,.8);z-index:3;display:flex;align-items:center;justify-content:center}

/* section heads */
.sec-head{position:absolute;left:0;width:1200px;text-align:center;color:var(--navy)}
.sec-head .divider-mark i{color:var(--navy)}
.sec-head h2{margin-top:14px;font-size:48px;font-weight:800;letter-spacing:.5px}
.left-head{position:absolute;left:100px;color:var(--navy)}
.left-head .divider-mark{justify-content:flex-start}
.left-head h2{margin-top:12px;font-size:48px;font-weight:800;letter-spacing:.5px}

/* about */
.about-lead{position:absolute;left:102px;top:1004px;width:470px;font-size:15px;line-height:25px;font-weight:600;color:var(--ink)}
.about-text{position:absolute;left:102px;width:470px;font-size:12.5px;line-height:23px;color:var(--body)}
.about-frame{position:absolute;left:619px;top:834px;width:192px;height:560px;background:var(--mist)}
.about-photo{position:absolute;left:663px;top:866px;width:437px;height:541px;background:linear-gradient(180deg,#2f7fe0 0%,#6aa8ee 45%,#cfe2f5 70%,#8a8c7a 100%)}

/* services */
.tile{position:absolute;overflow:hidden}
.tile .photo{position:absolute;inset:0}
.tile .shade{position:absolute;inset:0;background:linear-gradient(180deg,rgba(24,28,70,0) 35%,rgba(24,28,70,.92) 100%)}
.tile h3{position:absolute;left:37px;bottom:62px;color:var(--white);font-size:18px;line-height:28px;font-weight:700;letter-spacing:.3px}

/* projects */
.tabs{position:absolute;top:2910px;left:332px;display:flex;gap:18px}
.tab{width:168px;height:40px;display:flex;align-items:center;justify-content:center;background:var(--tab);color:var(--navy);font-size:11px;font-weight:700;letter-spacing:.3px}
.tab.active{background:var(--navy);color:var(--white)}
.proj-block{position:absolute;left:320px;top:3400px;width:326px;height:160px;background:var(--mist)}
.proj-photo{position:absolute;left:100px;top:3029px;width:498px;height:496px;background:linear-gradient(160deg,#b8c8dc 0%,#8e9aa8 40%,#d0b59a 70%,#8a9a6e 100%)}
.proj-card{position:absolute;left:556px;top:3088px;width:544px;height:382px;background:var(--white);box-shadow:0 6px 24px rgba(30,36,96,.14)}
.proj-card h3{position:absolute;left:44px;top:76px;font-size:24px;font-weight:800;color:var(--navy)}
.proj-card .lead{position:absolute;left:44px;top:125px;width:450px;font-size:14px;line-height:25px;font-weight:600;color:var(--ink)}
.proj-card .text{position:absolute;left:44px;top:186px;width:460px;font-size:12px;line-height:22px;color:var(--body)}
.proj-card .btn{left:44px;top:275px;width:136px;height:40px}
.sq-arrow{position:absolute;width:25px;height:25px;display:flex;align-items:center;justify-content:center}

/* news */
.news-arrows{position:absolute;top:3752px;left:1010px;display:flex;gap:20px}
.news-card{position:absolute;top:3880px;width:404px}
.news-card .photo{height:280px}
.news-card .cat{margin-top:56px;font-size:13px;font-weight:600;color:var(--ink)}
.news-card h4{margin-top:18px;font-size:17px;line-height:29px;font-weight:600;color:var(--ink)}
.news-card .meta{margin-top:20px;font-size:13px;color:var(--muted)}
.pylons{position:absolute;left:0;top:4300px;width:1200px;height:455px;background:linear-gradient(180deg,#ffffff 0%,#e9e6e0 25%,#c9b9a0 60%,#8d7a62 85%,#5a4f45 100%)}

/* footer */
.footer{position:absolute;left:0;top:4755px;width:1200px;height:631px;background:var(--navy)}
.footer .left-head{color:var(--white);top:86px}
.footer .left-head .divider-mark i{color:var(--white)}
.sub-note{position:absolute;left:713px;top:90px;width:390px;font-size:14px;line-height:27px;color:#c9cce6}
.sub-input{position:absolute;left:713px;top:153px;width:387px;height:47px;background:var(--white);display:flex;align-items:center;justify-content:space-between;padding:0 20px;font-size:14px;color:var(--ink)}
.rule{position:absolute;left:100px;width:1000px;height:1px;background:rgba(255,255,255,.22)}
.fcol{position:absolute;top:322px;color:var(--white)}
.fcol h5{font-size:14px;font-weight:700;letter-spacing:.3px;margin-bottom:18px}
.fcol li{list-style:none;font-size:13px;line-height:26px;color:#e6e8f5}
.contact li{display:flex;gap:14px;align-items:flex-start;line-height:25px}
.contact svg{flex:none;margin-top:6px}
.copyright{position:absolute;left:0;top:570px;width:1200px;text-align:center;font-size:13px;color:#e6e8f5}
</style>
</head>
<body>

<!-- Hero -->
<section class="hero" role="img" aria-label="Electrician in high-visibility vest working among substation equipment and power lines"></section>
<div class="brand"><span class="brand-mark"></span>BRISKET &amp; VANE</div>
<nav class="nav">
  <a class="active" href="#">HOME</a><a href="#">ABOUT</a><a href="#">SERVICES</a><a href="#">NEWS &amp; EVENTS</a><a href="#">CONTACT</a>
</nav>
<a class="btn quote">Request Quote</a>
<div class="hero-copy">
  <div class="divider-mark"><span></span><i></i><span></span></div>
  <p class="eyebrow">POWERING WHAT’S NEXT</p>
  <h1><span class="accent">RELIABLE. MODERN.</span><br>ELECTRICAL CONTRACTING<br>THAT MOVES WITH YOU.</h1>
</div>
<a class="btn play">Play Video
  <svg width="10" height="12" viewBox="0 0 10 12"><path d="M0 0L10 6L0 12Z" fill="#fff"/></svg>
</a>
<div class="scroll-bowl"></div>
<div class="scroll-btn">
  <svg width="22" height="22" viewBox="0 0 22 22" fill="none" stroke="#fff" stroke-width="2"><circle cx="11" cy="11" r="9"/><path d="M11 6v10M7 12l4 4 4-4"/></svg>
</div>

<!-- About -->
<div class="left-head" style="top:848px">
  <div class="divider-mark"><i></i><span></span></div>
  <h2>ABOUT US</h2>
</div>
<p class="about-lead">Sed ut perspiciatis unde omnis iste error sit voluptatem accusantium doloremque laudantium, totam raperiam, eaque ipsa quallo inventore veritatis et quasi.</p>
<p class="about-text" style="top:1094px">Nemo enim ipsam voluptatem quia voluptas sit aspernatur aut odit aut fugit, sed quia consequuntur magni dolores eos qui ratione vo luptatem sequi nesciunt. Neque porro quisquam est, qui dolorem ipsum quia dolor sit amet, consectetur, adipisci velit, sed quia non numquam eius modi tempora incidunt ut labore et dolore magnm aliquam quaerat voluptatem. Ut enim ad minima veniam, quis nos trum exercitationem ullam corporis suscipit laboriosam.</p>
<p class="about-text" style="top:1268px">Voluptatem quia voluptas sit aspernatur aut odit aut fugit, sed quia consequuntur magni dolores ene vo luptatem sequi nesciunt.</p>
<a class="btn" style="left:100px;top:1361px;width:138px;height:42px">Learn More</a>
<div class="about-frame"></div>
<div class="about-photo" role="img" aria-label="Lineman in a bucket lift working on a utility pole under a blue sky"></div>

<!-- Services -->
<div class="sec-head" style="top:1560px">
  <div class="divider-mark"><span></span><i></i><span></span></div>
  <h2>OUR SERVICES</h2>
</div>
<div class="tile" style="left:0;top:1750px;width:598px;height:437px">
  <div class="photo" role="img" aria-label="Electrician installing overhead lighting in a warehouse" style="background:linear-gradient(160deg,#8fa2b8,#4e5a70 55%,#c07a3a)"></div><div class="shade"></div>
  <h3>ELECTRICAL<br>INSTALLATIONS</h3>
</div>
<div class="tile" style="left:598px;top:1750px;width:303px;height:437px">
  <div class="photo" role="img" aria-label="Technician testing an outdoor electrical panel" style="background:linear-gradient(160deg,#a8845e,#d7d2c8 45%,#5a6478)"></div><div class="shade"></div>
  <h3>DESIGN-BUILD<br>PROJECTS</h3>
</div>
<div class="tile" style="left:901px;top:1750px;width:299px;height:437px">
  <div class="photo" role="img" aria-label="Power lines above a line of trees" style="background:linear-gradient(180deg,#c8d2d4,#6f8a78 55%,#3e4f48)"></div><div class="shade"></div>
  <h3>EMERGENCY<br>SERVICES</h3>
</div>
<div class="tile" style="left:0;top:2187px;width:293px;height:437px">
  <div class="photo" role="img" aria-label="Worker silhouetted against a sunset at a substation" style="background:linear-gradient(160deg,#3d3440,#b8733e 50%,#2a2a3a)"></div><div class="shade"></div>
  <h3>ENERGY-EFFICIENT<br>SOLUTIONS</h3>
</div>
<div class="tile" style="left:293px;top:2187px;width:305px;height:437px">
  <div class="photo" role="img" aria-label="Electrician servicing an open switch cabinet" style="background:linear-gradient(160deg,#c9ccd2,#7c8595 45%,#c28a4a 75%,#3a3f55)"></div><div class="shade"></div>
  <h3>MAINTENANCE &amp;<br>UPGRADES</h3>
</div>
<div class="tile" style="left:598px;top:2187px;width:602px;height:437px">
  <div class="photo" role="img" aria-label="Technician wiring an industrial control unit" style="background:linear-gradient(160deg,#6d4a34,#8a98a6 45%,#4a5566)"></div><div class="shade"></div>
  <h3>SMART SYSTEMS &amp;<br>AUTOMATION</h3>
</div>

<!-- Projects -->
<div class="sec-head" style="top:2762px">
  <div class="divider-mark"><span></span><i></i><span></span></div>
  <h2>OUR PROJECTS</h2>
</div>
<div class="tabs">
  <div class="tab">RESIDENTIAL</div><div class="tab active">COMMERCIAL</div><div class="tab">INDUSTRIAL</div>
</div>
<div class="proj-block"></div>
<div class="proj-photo" role="img" aria-label="Engineer in safety vest inspecting substation switchgear"></div>
<div class="proj-card">
  <h3>COMMERCIAL PROJECT</h3>
  <p class="lead">Duis aute irure dolor in reprehenderit in voluptate velit esse cillum dolore eu fugiat nulla pariatur</p>
  <p class="text">Sed ut perspiciatis unde omnis iste natus error sit voluptatem accu­santium doloremque laudantium, totam rem aperiam, eaque ipsa quae ab illo inventore veritatis et quasi.</p>
  <a class="btn">Learn More</a>
  <div class="sq-arrow" style="left:466px;top:338px;background:#fbd8ab">
    <svg width="13" height="10" viewBox="0 0 13 10" fill="none" stroke="#fff" stroke-width="1.6"><path d="M12 5H1M5 1L1 5l4 4"/></svg>
  </div>
  <div class="sq-arrow" style="left:502px;top:338px;background:var(--orange)">
    <svg width="13" height="10" viewBox="0 0 13 10" fill="none" stroke="#fff" stroke-width="1.6"><path d="M1 5h11M8 1l4 4-4 4"/></svg>
  </div>
</div>

<!-- News -->
<div class="left-head" style="top:3685px">
  <div class="divider-mark"><i></i><span></span></div>
  <h2>NEWS &amp; EVENTS</h2>
</div>
<div class="news-arrows">
  <svg width="36" height="20" viewBox="0 0 36 20" fill="none" stroke="#b7b9c4" stroke-width="2"><path d="M35 10H2M10 2L2 10l8 8"/></svg>
  <svg width="36" height="20" viewBox="0 0 36 20" fill="none" stroke="#1f2233" stroke-width="2"><path d="M1 10h33M26 2l8 8-8 8"/></svg>
</div>
<div class="pylons" role="img" aria-label="Transmission towers silhouetted against an evening sky"></div>
<article class="news-card" style="left:100px">
  <div class="photo" role="img" aria-label="Engineers in hard hats reviewing plans on a laptop" style="background:linear-gradient(160deg,#5a5040,#b6a84a 45%,#3c3a40)"></div>
  <p class="cat">LOREM IPSUM</p>
  <h4>Nostrum exercitationem ullam corpo ris suscipit laboriosam, nisiquid</h4>
  <p class="meta">By Dana Ortwell &nbsp;| &nbsp;Apr 18, 2025</p>
</article>
<article class="news-card" style="left:543px">
  <div class="photo" role="img" aria-label="Engineer with a tablet near wind turbines" style="background:linear-gradient(180deg,#dfe4e6,#b9bfbc 50%,#8a8f6e)"></div>
  <p class="cat">LOREM IPSUM</p>
  <h4>Nostrum exercitationem ullam corpo ris suscipit laboriosam, nisiquid</h4>
  <p class="meta">By Dana Ortwell &nbsp;| &nbsp;Apr 18, 2025</p>
</article>
<article class="news-card" style="left:987px">
  <div class="photo" role="img" aria-label="Workers on an industrial construction site" style="background:linear-gradient(160deg,#6a5548,#a89888 50%,#4a4240)"></div>
  <p class="cat">LOREM IPSUM</p>
  <h4>Nostrum exercitationem ullam corpo ris suscipit laboriosam, nisiquid</h4>
  <p class="meta">By Dana Ortwell &nbsp;| &nbsp;Apr 18, 2025</p>
</article>

<!-- Footer -->
<footer class="footer">
  <div class="left-head">
    <div class="divider-mark"><i></i><span></span></div>
    <h2>SUBSCRIBE TO US</h2>
  </div>
  <p class="sub-note">Get updates on our latest projects, electrical innovations, and industry news.</p>
  <div class="sub-input"><span>Email Us</span>
    <svg width="24" height="16" viewBox="0 0 24 16" fill="none" stroke="#f7941d" stroke-width="2"><path d="M1 8h21M15 1l7 7-7 7"/></svg>
  </div>
  <div class="rule" style="top:270px"></div>
  <div class="fcol contact" style="left:100px">
    <h5>CONTACT US</h5>
    <ul>
      <li><svg width="10" height="13" viewBox="0 0 10 13"><path d="M5 0a5 5 0 0 1 5 5c0 3.5-5 8-5 8S0 8.5 0 5a5 5 0 0 1 5-5z" fill="#fff"/><circle cx="5" cy="5" r="1.8" fill="#1e2460"/></svg><span>Brisket &amp; Vane Electrical<br>Contracting, Address comes here</span></li>
      <li><svg width="12" height="9" viewBox="0 0 12 9"><rect width="12" height="9" rx="1" fill="#fff"/><path d="M0.5 0.8L6 5l5.5-4.2" fill="none" stroke="#1e2460"/></svg><span>info@brisket-vane.example</span></li>
      <li><svg width="11" height="11" viewBox="0 0 24 24"><path d="M6.6 10.8a15 15 0 0 0 6.6 6.6l2.2-2.2a1 1 0 0 1 1-.25 11.4 11.4 0 0 0 3.6.57 1 1 0 0 1 1 1V20a1 1 0 0 1-1 1A17 17 0 0 1 3 4a1 1 0 0 1 1-1h3.5a1 1 0 0 1 1 1c0 1.25.2 2.45.57 3.57a1 1 0 0 1-.25 1z" fill="#fff"/></svg><span>+1 555-010-4477</span></li>
    </ul>
  </div>
  <div class="fcol" style="left:439px">
    <h5>QUICK LINKS</h5>
    <ul><li>Home</li><li>About Us</li><li>Our Services</li><li>Our Projects</li></ul>
  </div>
  <div class="fcol" style="left:661px">
    <h5>OTHER LINKS</h5>
    <ul><li>Contact Us</li><li>Terms &amp; Conditions</li><li>Privacy Policy</li><li>Cookies</li></ul>
  </div>
  <div class="fcol" style="left:916px">
    <h5>WORKING HOURS</h5>
    <ul><li>Mon- Fri: 9am-10pm</li><li>Sat: 11am- 5pm</li><li>Sunday: Closed</li></ul>
  </div>
  <div class="rule" style="top:534px"></div>
  <p class="copyright">Copyright © 2025 Brisket &amp; Vane Electrical Contracting . All rights reserved.</p>
</footer>

</body>
</html>
```